Cleaning service website design

We need a new nice web design(logo will be the same) for a new cleaning service Company:

Informations about Company and logo you can take from flyers in attachments.

This is a cleaning service Company which have simple rules and we would like to show that(in checklist form) on website:

- What we do and that we're Cleaning Green

- Why us?

- How much(our pricing is simple)

Also we would like to communicate with clients by some nice/big pictures on website and the most important thing is our phone number and short/fast Brimtallow.

Also there should be some space for description about our Company.

Generally all information on main page can be short: about us, about service(what we do), last reviews, tips (for example: Tip of the week) and other can be some introduction to subpage where will be more information.

There will be few subpages like: About us, About our service, Photos(Before and after), Reviews , Tips, FAQ, Contact, Looking for a Job? - most of them will be just text so you can project just one example.

```html
<!DOCTYPE html>
<html lang="en">
<head>
<meta charset="utf-8">
<title>Tidy Fern – House Cleaning</title>
<link href="https://fonts.googleapis.com/css2?family=Source+Sans+3:ital,wght@0,400;0,600;0,700;1,400&family=PT+Sans+Narrow:wght@700&display=swap" rel="stylesheet">
<style>
:root{
  --green:#79bf2a;
  --green-dark:#4f8a1c;
  --blue:#1660b0;
  --ink:#222;
  --text:#333;
  --muted:#999;
  --line:#d5d5d5;
  --orange:#f38a00;
  --orange-light:#ffb21a;
  --red:#e11b1b;
  --panel:#fafafa;
}
*{box-sizing:border-box;margin:0;padding:0}
html,body{width:1200px;height:1042px;overflow:hidden;background:#fff}
body{font-family:"Source Sans 3",sans-serif;color:var(--text);position:relative}
.header{position:absolute;left:0;top:0;width:1200px;height:127px;border-bottom:6px solid #ececec}
.brand{position:absolute;left:150px;top:40px;display:flex;align-items:center;gap:10px;font-weight:700;font-size:34px;color:var(--green-dark)}
.brand-dot{width:26px;height:26px;border-radius:50%;background:var(--green)}
.callbox{position:absolute;right:150px;top:13px;text-align:right}
.callbox small{font-size:14px;color:var(--ink)}
.callbox small b{font-weight:700}
.callbox .phone{display:flex;align-items:center;justify-content:flex-end;gap:6px;font-size:27px;font-weight:700;color:#111;line-height:1.1}
.nav{position:absolute;right:150px;top:66px;display:flex;height:61px}
.nav a{font-family:"PT Sans Narrow",sans-serif;font-size:13.5px;color:#333;text-decoration:none;padding:23px 16px 0;letter-spacing:.2px}
.nav a.active{background:#f1f1f1;color:var(--green);border-bottom:4px solid var(--green)}
.hero{position:absolute;left:0;top:134px;width:1200px;height:503px;background:radial-gradient(ellipse at 80% 40%,#8aa25a 0,#486f2c 30%,#2c5a22 60%,#1d3f18 100%)}
.hero-copy{position:absolute;left:149px;top:50px;color:#fff}
.hero h1{font-size:42px;font-weight:400;letter-spacing:.5px;line-height:1}
.hero h1 b{font-weight:700}
.hero .sub{margin-top:12px;font-size:23px;font-weight:600}
.hero .sub em{font-style:normal;color:var(--red);font-size:40px;font-weight:700;margin-left:3px}
.checklist{list-style:none;margin-top:8px}
.checklist li{display:flex;align-items:center;gap:12px;font-size:15.5px;font-weight:600;height:33.6px}
.cta{position:absolute;left:149px;top:376px;width:247px;height:58px;border-radius:5px;background:linear-gradient(var(--orange-light),var(--orange));color:#fff;font-size:27px;font-weight:700;display:flex;align-items:center;justify-content:center;gap:12px}
.badge{position:absolute;left:424px;top:364px;width:70px;height:70px;border-radius:50%;background:radial-gradient(circle at 40% 35%,#fff,#cfe9b0)}
.card{position:absolute;top:674px;width:288px;height:342px;background:var(--panel);border:1px solid var(--line);box-shadow:0 6px 6px -4px #bbb}
.card .photo{margin:5px;height:109px;background:linear-gradient(90deg,#c9a27a,#e9d9c5,#a98561)}
.card h2{color:var(--green);font-size:21px;font-weight:600;text-align:center;margin-top:11px}
.bullets{list-style:none;margin:17px 0 0 30px;font-size:14px;line-height:19px}
.bullets li{position:relative;padding-left:18px;margin-bottom:9px}
.bullets li:before{content:"";position:absolute;left:0;top:7px;width:6px;height:6px;background:#222}
.prices{margin:17px 0 0 38px;font-size:14px;line-height:19px}
.prices p{margin-bottom:4.5px}
.prices b{color:var(--green);font-weight:400}
.prices a{color:var(--blue)}
.prices .note{font-style:italic;font-size:12px;margin-top:31px}
.estimate h2{margin-top:18px;font-size:21px}
.field{position:absolute;left:30px;width:225px;height:29px;border:1px solid #ccc;background:#fff;font-size:11px;color:var(--muted);padding:8px 12px}
.field.half{width:109px}
.callnow{position:absolute;left:32px;top:298px;font-size:11px;font-weight:700;color:#111;line-height:1.1}
.callnow span{display:block;font-size:19px;color:var(--blue)}
.submit{position:absolute;left:173px;top:298px;width:88px;height:28px;background:linear-gradient(var(--orange-light),var(--orange));color:#fff;font-size:13px;font-weight:700;text-align:center;line-height:28px;border-radius:2px}
</style>
</head>
<body>
<header class="header">
  <div class="brand"><span class="brand-dot"></span>Tidy Fern</div>
  <div class="callbox">
    <small><b>Call Us</b> to arrange your cleaning on</small>
    <div class="phone">
      <svg width="18" height="22" viewBox="0 0 18 22"><path d="M4 1l4 5-2 3c1 3 3 6 6 8l3-2 3 4-3 3C8 21 1 12 1 4z" fill="#1660b0"/></svg>
      555-014-2280
    </div>
  </div>
  <nav class="nav">
    <a class="active">HOME</a><a>ABOUT US</a><a>OUR SERVICES</a><a>PHOTOS</a><a>REVIEWS</a><a>TIPS</a><a>CAREERS</a><a>FAQ</a><a>CONTACT</a>
  </nav>
</header>

<section class="hero" role="img" aria-label="Woman with outstretched arms in a lush green forest with a waterfall">
  <div class="hero-copy">
    <h1>SIMPLIFY <b>YOUR LIFE</b></h1>
    <p class="sub">and some there House Cleaning from <em>$79</em></p>
    <ul class="checklist">
      <li><svg width="22" height="24" viewBox="0 0 22 24"><path d="M2 22C2 10 10 3 21 1c0 12-8 20-19 21z" fill="#7cc52a"/></svg>Locally Owned &amp; Operated</li>
      <li><svg width="22" height="24" viewBox="0 0 22 24"><path d="M2 22C2 10 10 3 21 1c0 12-8 20-19 21z" fill="#7cc52a"/></svg>Reliable &amp; Affordable</li>
      <li><svg width="22" height="24" viewBox="0 0 22 24"><path d="M2 22C2 10 10 3 21 1c0 12-8 20-19 21z" fill="#7cc52a"/></svg>All Supplies Provided</li>
      <li><svg width="22" height="24" viewBox="0 0 22 24"><path d="M2 22C2 10 10 3 21 1c0 12-8 20-19 21z" fill="#7cc52a"/></svg>No Contracts</li>
      <li><svg width="22" height="24" viewBox="0 0 22 24"><path d="M2 22C2 10 10 3 21 1c0 12-8 20-19 21z" fill="#7cc52a"/></svg>Pet Friendly</li>
      <li><svg width="22" height="24" viewBox="0 0 22 24"><path d="M2 22C2 10 10 3 21 1c0 12-8 20-19 21z" fill="#7cc52a"/></svg>Green Cleaning</li>
    </ul>
  </div>
  <div class="cta">GET STARTED
    <svg width="30" height="26" viewBox="0 0 30 26"><path d="M1 8h15V1l13 12-13 12v-7H1z" fill="#fff"/></svg>
  </div>
  <div class="badge"></div>
</section>

<article class="card" style="left:148px">
  <div class="photo" role="img" aria-label="Smiling family with their dog on a sofa"></div>
  <h2>What do we clean?</h2>
  <ul class="bullets">
    <li>Thoroughly clean your bathrooms, kitchen, bedrooms and living areas</li>
    <li>Mop or vacuum your floors</li>
    <li>Dust surfaces</li>
    <li>Collect garbage</li>
    <li>Make beds</li>
  </ul>
</article>

<article class="card" style="left:455px">
  <div class="photo" role="img" aria-label="Family looking at a laptop together"></div>
  <h2>Pricing is..simple</h2>
  <div class="prices">
    <p><b>$79</b> for homes less than 1000 sq ft</p>
    <p><b>$89</b> for homes 1000-1800 sq ft</p>
    <p><b>$99</b> for homes 1800-2600 sq ft</p>
    <p>If your home is larger than 2600 sq ft please <a>call for a quote</a></p>
    <p class="note">*rates are for regular service*</p>
  </div>
</article>

<aside class="card estimate" style="left:761px">
  <h2>Quick Free Estimate</h2>
  <div class="field" style="top:56px">Name</div>
  <div class="field" style="top:98px">E-mail</div>
  <div class="field" style="top:140px">Postal Code</div>
  <div class="field" style="top:182px">Phone</div>
  <div class="field half" style="top:224px">No. of Bathrooms</div>
  <div class="field half" style="top:224px;left:146px">No. of Bedrooms</div>
  <div class="callnow">CALL US TODAY<span>555-014-2280</span></div>
  <div class="submit">SUBMIT</div>
</aside>
</body>
</html>
```